Government Contracting business needs a website design.

Pellworth & Quine, LLC is a minority owned Service Disabled Veteran Owned Small Business (SDVOSB) that provides Strategic Planning, Public Health Emergency Response, and Data Management Solutions for Federal Civilian and Defense Agencies. We have over 20 years of experience helping health and defense agencies develop concept of operations, deploy assets and personnel in Hot Zones around the world, and deliver goods and services all of the globe.

We are a leader in the field of Data Management. We help our customers develop cloud migration and disaster recovery strategies. We are experts with database management, data replication, queries, consolidation, and records management.

We are looking for a very nice and simple website designs that states clearly what we do as a company and that is easy for our customers to follow. We would like to have some moving pictures that are base on our expertise. We want the website to be easy to use and have the scroll down features that keeps things all on the same page when clicking on the menu. I attached a document with what we need on the website. I will also attach our logo. We want it to look simple clean and very professional.

Target Market(s)

Government Contracting, Management Consulting, Health

Industry/Entity Type

Government

Coding

Coded - Design and coding required

Number of Pages Required

1 page

Font styles to use
Serif

Requirements
Must have
• Very nice picture slides that speaks to our capabilities in Disaster Response, Strategic Planning, and Database Management. Slick look and design. Make sure SDVOSB Logo is right at the beginning of website as our customers is looking for that certification. Very nice colors that blend well with our logo.
Nice to have
• Very nice and slick colors that blends well with logo.
Should not have
• Basic website design that are weary on the eye. No bright colors, just simple colors that looks good with logo.

```html
<!DOCTYPE html>
<html lang="en">
<head>
<meta charset="utf-8">
<title>Pellworth &amp; Quine, LLC</title>
<link href="https://fonts.googleapis.com/css2?family=Libre+Baskerville:ital,wght@0,400;0,700;1,400&family=Open+Sans:wght@400;600;700&display=swap" rel="stylesheet">
<style>
:root{
  --navy:#2c495d;
  --slate:#3a596d;
  --slate-deep:#2f4b5e;
  --ink:#333c44;
  --muted:#5d6870;
  --light:#ececec;
  --white:#ffffff;
  --line:#c7cfd5;
}
*{box-sizing:border-box;margin:0;padding:0}
html,body{width:1200px;height:3656px;overflow:hidden}
body{font-family:"Open Sans",Arial,sans-serif;color:var(--ink);background:var(--white);position:relative}
.serif{font-family:"Libre Baskerville",Georgia,serif}

/* header */
.site-header{position:absolute;top:0;left:0;width:1200px;height:112px;background:var(--navy);display:flex;align-items:center;justify-content:space-between;padding:0 64px 0 72px}
.brand{display:flex;align-items:center;gap:14px;color:var(--white)}
.brand-mark{width:40px;height:40px;border:2px solid var(--white)}
.brand-name{font-family:"Libre Baskerville",Georgia,serif;font-size:24px}
.nav{display:flex;gap:8px}
.nav a{color:var(--white);text-decoration:none;font-size:15px;letter-spacing:.5px;padding:14px 20px}
.nav a.active{background:var(--white);color:var(--navy);font-weight:600}

/* hero */
.hero{position:absolute;top:112px;left:0;width:1200px;height:624px;background:linear-gradient(100deg,#5b6f80 0%,#8a96a0 38%,#6a6a72 62%,#3a4250 100%)}
.hero-copy{position:absolute;left:80px;top:140px;width:360px;color:var(--white)}
.hero-copy h1{font-family:"Libre Baskerville",Georgia,serif;font-weight:400;font-size:34px;line-height:1.3}
.hero-copy p{font-family:"Libre Baskerville",Georgia,serif;font-style:italic;font-size:17px;line-height:1.5;margin-top:18px}
.btn{display:inline-block;background:var(--navy);color:var(--white);font-size:15px;font-weight:700;letter-spacing:.5px;padding:14px 24px;text-decoration:none}
.btn-outline{border:2px solid var(--white);background:rgba(44,73,93,.6)}
.hero-copy .btn{margin-top:26px}
.cert-badge{position:absolute;left:844px;top:332px;width:200px;height:200px;border-radius:50%;border:6px solid var(--white);background:rgba(44,73,93,.45)}

/* about */
.about{position:absolute;top:736px;left:0;width:1200px;height:424px}
.section-title{font-family:"Libre Baskerville",Georgia,serif;font-weight:400;font-size:36px;color:var(--navy);display:flex;align-items:center;gap:14px}
.section-title::after{content:"";width:90px;height:2px;background:currentColor}
.about .section-title{position:absolute;left:80px;top:60px}
.about p{position:absolute;left:80px;top:136px;width:600px;font-size:15px;line-height:1.6;color:var(--muted)}
.about .btn{position:absolute;left:80px;top:288px}
.about-photo{position:absolute;left:808px;top:56px;width:264px;height:264px;border-radius:50%;border:8px solid var(--navy);background:linear-gradient(135deg,#8c7a66,#c9b79e 50%,#5d4d40)}

/* capabilities */
.capabilities{position:absolute;top:1160px;left:0;width:1200px;height:600px;background:var(--slate)}
.capabilities h2{position:absolute;top:56px;width:1200px;text-align:center;font-family:"Libre Baskerville",Georgia,serif;font-weight:400;font-size:40px;color:var(--white)}
.capabilities h2::before,.capabilities h2::after{content:"";display:inline-block;width:80px;height:2px;background:var(--white);vertical-align:middle;margin:0 18px}
.cap-card{position:absolute;width:440px;height:208px;background:var(--white);padding:26px 28px}
.cap-card h3{font-size:18px;font-weight:600;color:var(--navy);margin-bottom:10px}
.cap-card ul{list-style:none;font-size:14px;line-height:1.7;color:var(--muted)}
.cap-card li::before{content:"";display:inline-block;width:6px;height:6px;background:var(--navy);border-radius:50%;margin-right:10px;vertical-align:middle}
.cap-card .more{display:inline-block;margin-top:8px;font-size:12px;font-weight:700;color:var(--navy);border-bottom:2px solid var(--navy)}
.cap-icon{position:absolute;top:56px;width:96px;height:96px;border-radius:50%;background:var(--white);border:3px solid var(--navy);display:flex;align-items:center;justify-content:center}
.cap-card.left{left:80px}.cap-card.left .cap-icon{right:28px}
.cap-card.right{left:680px;padding-left:160px}.cap-card.right .cap-icon{left:28px}
.cap-card.left{padding-right:150px}
.row1{top:112px}.row2{top:360px}
.cap-center{position:absolute;left:540px;top:282px;width:120px;text-align:center;color:var(--white);font-family:"Libre Baskerville",Georgia,serif;font-size:16px;line-height:1.4}
.cap-center span{display:block;width:44px;height:44px;border-radius:50%;border:2px solid var(--white);margin:0 auto 10px}

/* partners */
.partners{position:absolute;top:1760px;left:0;width:1200px;height:240px;display:flex;align-items:center;justify-content:center;gap:56px}
.partner{width:150px;height:150px;border-radius:50%;background:#d9dee2;border:4px solid #b6c0c8}
.partner.square{border-radius:0;width:170px;height:110px}

/* why */
.why{position:absolute;top:2000px;left:0;width:1200px;height:440px;background:var(--light)}
.why-photo{position:absolute;left:80px;top:80px;width:440px;height:280px;background:linear-gradient(120deg,#c9ccd0,#8e9aa6 55%,#4e5f6e)}
.why .section-title{position:absolute;left:620px;top:52px}
.why ul{position:absolute;left:620px;top:120px;width:480px;list-style:none;font-size:14px;line-height:1.55;color:var(--muted)}
.why li{position:relative;padding-left:24px;margin-bottom:12px}
.why li::before{content:"";position:absolute;left:2px;top:7px;width:8px;height:8px;background:var(--navy);border-radius:50%}
.why .btn{position:absolute;left:620px;top:350px}

/* join */
.join{position:absolute;top:2440px;left:0;width:1200px;height:460px;text-align:center}
.join .section-title{justify-content:center;margin-top:60px}
.join .section-title::before{content:"";width:90px;height:2px;background:currentColor}
.join p{width:820px;margin:24px auto 0;font-size:14px;line-height:1.65;color:var(--muted)}
.join h4{margin-top:24px;font-size:17px;font-weight:600;color:var(--navy)}
.join p.small{margin-top:12px}
.join .btn{margin-top:24px;font-size:13px;padding:12px 20px}

/* contact */
.contact{position:absolute;top:2900px;left:0;width:1200px;height:660px;background:var(--slate-deep)}
.contact .section-title{position:absolute;left:80px;top:56px;color:var(--white)}
.contact-form{position:absolute;left:80px;top:128px;width:660px;display:grid;grid-template-columns:1fr 1fr;gap:14px 20px}
.field{height:52px;border:1px solid var(--line);color:var(--white);font-size:14px;padding:15px 16px;background:rgba(255,255,255,.04)}
.field.message{grid-column:1/3;height:112px}
.submit{grid-column:1/3;height:48px;background:var(--white);color:var(--navy);font-weight:700;font-size:16px;letter-spacing:1px;display:flex;align-items:center;justify-content:center}
.contact-photo{position:absolute;left:840px;top:56px;width:280px;height:604px;background:linear-gradient(180deg,#6c8597,#a7b7c3 45%,#5a7487)}

/* footer */
.site-footer{position:absolute;top:3560px;left:0;width:1200px;height:96px;display:flex;align-items:center;justify-content:space-between;padding:0 80px;font-size:13px;color:var(--muted)}
.footer-brand{font-family:"Libre Baskerville",Georgia,serif;color:var(--navy);font-size:16px;position:absolute;left:0;width:1200px;text-align:center;pointer-events:none}
.social{display:flex;gap:12px}
.social span{width:36px;height:36px;border-radius:50%;background:var(--navy)}
</style>
</head>
<body>

<header class="site-header">
  <div class="brand"><span class="brand-mark"></span><span class="brand-name">Pellworth &amp; Quine</span></div>
  <nav class="nav">
    <a class="active" href="#home">HOME</a>
    <a href="#about">ABOUT US</a>
    <a href="#capabilities">CORE CAPABILITIES</a>
    <a href="#why">WHY HIRE US</a>
    <a href="#join">JOIN US</a>
  </nav>
</header>

<section class="hero" id="home" role="img" aria-label="Slide photo of government officials at a briefing with flags in the background">
  <div class="hero-copy">
    <h1>LOREM IPSUM IS SIMPLY DUMMY</h1>
    <p>Lorem Ipsum is simply dummy text of the printing and typesetting</p>
    <a class="btn btn-outline" href="#about">LEARN MORE</a>
  </div>
  <div class="cert-badge" role="img" aria-label="SDVOSB certification badge"></div>
</section>

<section class="about" id="about">
  <h2 class="section-title">About us</h2>
  <p>Pellworth &amp; Quine, LLC is a minority owned Service Disabled Veteran Owned Small Business (SDVOSB) that provides Strategic Planning, Public Health Emergency Response, and Data Management Solutions for Federal Civilian and Defense Agencies. We have over 20 years of experience helping health and defense agencies develop concept of operation.</p>
  <a class="btn" href="#capabilities">LEARN MORE</a>
  <div class="about-photo" role="img" aria-label="Photo of a team meeting around a conference table"></div>
</section>

<section class="capabilities" id="capabilities">
  <h2>Core Capabilities</h2>

  <article class="cap-card left row1">
    <h3>Strategic Planning</h3>
    <ul><li>Organizational Needs Assessment</li><li>Roadmap Development</li><li>Marketing Outreach</li></ul>
    <span class="more">READ MORE</span>
    <div class="cap-icon"><svg width="48" height="48" viewBox="0 0 48 48" fill="none" stroke="#2c495d" stroke-width="3"><rect x="18" y="4" width="12" height="10"/><rect x="4" y="34" width="12" height="10"/><rect x="32" y="34" width="12" height="10"/><path d="M24 14v10M10 34v-10h28v10"/></svg></div>
  </article>

  <article class="cap-card right row1">
    <h3>Public Health Emergency Response</h3>
    <ul><li>Crisis Management</li><li>Disaster Relief Planning</li><li>Assets and Personnel Deployment</li></ul>
    <span class="more">READ MORE</span>
    <div class="cap-icon"><svg width="48" height="48" viewBox="0 0 48 48"><rect x="4" y="12" width="40" height="30" rx="4" fill="#2c495d"/><rect x="16" y="6" width="16" height="8" fill="none" stroke="#2c495d" stroke-width="3"/><path d="M24 19v16M16 27h16" stroke="#fff" stroke-width="4"/></svg></div>
  </article>

  <div class="cap-center"><span></span>Pellworth &amp; Quine</div>

  <article class="cap-card left row2">
    <h3>Data Management Services</h3>
    <ul><li>Cloud Migration Strategy</li><li>Disaster Recovery Strategy</li><li>Records Management</li></ul>
    <span class="more">READ MORE</span>
    <div class="cap-icon"><svg width="48" height="48" viewBox="0 0 48 48" fill="none" stroke="#2c495d" stroke-width="3"><ellipse cx="24" cy="10" rx="15" ry="5"/><path d="M9 10v28c0 3 7 5 15 5s15-2 15-5V10M9 24c0 3 7 5 15 5s15-2 15-5"/></svg></div>
  </article>

  <article class="cap-card right row2">
    <h3>Contracts Vehicles</h3>
    <ul><li>SDVOSB Sole Source</li><li>GSA Schedule 70 SIN 132-51 (Sub)</li><li>GSA OASIS Pool 1 (Sub)</li></ul>
    <span class="more">READ MORE</span>
    <div class="cap-icon"><svg width="52" height="48" viewBox="0 0 52 48"><rect x="2" y="12" width="30" height="22" fill="#2c495d"/><path d="M32 18h10l8 8v8H32z" fill="#2c495d"/><circle cx="12" cy="38" r="5" fill="#fff" stroke="#2c495d" stroke-width="3"/><circle cx="40" cy="38" r="5" fill="#fff" stroke="#2c495d" stroke-width="3"/></svg></div>
  </article>
</section>

<section class="partners" aria-label="Agency clients">
  <div class="partner"></div>
  <div class="partner"></div>
  <div class="partner square"></div>
  <div class="partner square"></div>
  <div class="partner"></div>
</section>

<section class="why" id="why">
  <div class="why-photo" role="img" aria-label="Photo of business people shaking hands in an office"></div>
  <h2 class="section-title">Why Hire Us?</h2>
  <ul>
    <li>Over 20 years of experience deploying assets and personnel to disaster zones around the US and the world.</li>
    <li>Over 20 years of experience developing concept of operations and stakeholder management strategies for Federal Agencies.</li>
    <li>Over 15 years of experience with database management and replications.</li>
    <li>Highly educated consultants with over 90% possessing advanced degrees and relevant certifications.</li>
  </ul>
  <a class="btn" href="#join">LEARN MORE</a>
</section>

<section class="join" id="join">
  <h2 class="section-title">Join Us</h2>
  <p>Pellworth &amp; Quine strives to provide an outstanding work environment for our employees. We invest in our people and believe strongly in creating an environment where our employees are free to work on innovative solutions that meet our clients' needs. We promote true work-life balance, career advancement, health, and financial security and fun in the work place. We encourage our employees to participate in our internal operation and help to develop them into the ideal consultants that our clients want.</p>
  <h4>Job Openings</h4>
  <p class="small">We are always recruiting for key positions. If you want to bring your talent to us, submit your resume against the key positions we have below. We are recruiting junior, mid-level, senior as well as subject matter experts.</p>
  <a class="btn" href="#contact">UPLOAD RESUME</a>
</section>

<section class="contact" id="contact">
  <h2 class="section-title">Contact Us</h2>
  <form class="contact-form">
    <div class="field">Name</div>
    <div class="field">E-mail</div>
    <div class="field">Phone</div>
    <div class="field">Subject</div>
    <div class="field message">Message</div>
    <div class="submit">SUBMIT</div>
  </form>
  <div class="contact-photo" role="img" aria-label="Photo of a smiling professional holding a tablet"></div>
</section>

<footer class="site-footer">
  <span>© PELLWORTH &amp; QUINE - 2016. All Rights Reserved.</span>
  <span class="footer-brand">Pellworth &amp; Quine</span>
  <div class="social"><span></span><span></span><span></span></div>
</footer>

</body>
</html>
```